Morvel's Cocktail Bar & Cigar Lounge

PLEASE DO NOT START WORKING ON THIS PROJECT BEFORE YOU READ ALL OF THE TEXT!!!
Project Title
Morvel’s Cocktail Bar & Cigar Lounge — Full Website Design (Wix)
Project Overview
We are seeking a designer to create a sophisticated, 1920s-inspired website for Morvel’s Cocktail Bar & Cigar Lounge, located in Kilchberg, Zurichsee, Switzerland. The site will be built on Wix and must include an art deco, luxury look, clear booking functionality, and downloadable menu.

Brand & Visual Direction
Brand: Morvel’s Cocktail Bar & Cigar Lounge
Logo: Logo_morvels_bar_black.jpg
Style: 1920s-inspired, art deco, sophisticated luxury, timeless, exclusive, subtle spectacle
Color Palette: Emerald green, gold, black, cream
Icons/Motifs: Martini glass, cigar, champagne flute, art deco borders, geometric patterns
Typography: Elegant serif for headlines (e.g., Playfair Display, Cormorant Garamond); clean sans-serif for body (e.g., Lato, Open Sans, Montserrat)
Image Style: Moody, warm lighting; classic cocktails; vintage barware; subtle 1920s hints; lounge ambiance; cigars; elegant guests
Sitemap & Main Pages
Home
About
Events
Menu
Gallery
Reservations
Contact
Website Copy
Home
Zurich’s Most Exclusive Cocktail Bar & Cigar Lounge

Timeless sophistication. Intelligent indulgence. A sanctuary by the lake.

[Reserve Your Table] (CTA Button)
A New Era on the Lake

Morvel’s invites you into a world where elegance meets camaraderie, and every visit feels like a privilege. Step through our doors and discover a connoisseur’s sanctuary inspired by the golden age of the 1920s—reimagined for Zurich’s most discerning guests.
Signature Experiences Await
Ladies Night, Every Friday: Two cocktails for the price of one, exclusively for the ladies.
Saturday Event Series: Oyster Night, Pata Negra Night, Champagne & Caviar Night, and Vintage Havana Night—each a celebration of taste and refinement.
Curated Cocktails & Cigars: Savor our expertly crafted cocktails, rare spirits, and a handpicked selection of premium cigars.
Meet Your Hosts

In 2025, a new partnership brings fresh energy to Morvel’s. Hospitality expert Orla Venstrup (Lanternhook Productions) joins forces with renowned bar professional Pavel Ducray (Glass Keeper at Hand) to elevate your experience and set a new standard for luxury in Zurichsee.
Gallery Preview

[Slideshow or mosaic of atmospheric images: cocktails, lounge ambiance, cigars, elegant guests]
Reserve Your Table

Secure your place at Zurich’s most exclusive bar.

Phone: 076 418 63 57

Email: contact@morvels-example.ch

Online: www.morvels-example.ch
Footer:

Uferweg 14, 8802 Kilchberg, Switzerland

Open Tuesday–Saturday, 17:00–00:00 | October–March
About
Our Story

Morvel’s Cocktail Bar & Cigar Lounge was born from a passion for refined hospitality and a love for the timeless rituals of the world’s great bars. Inspired by the golden age of the 1920s, our lounge is a haven for those who appreciate intelligent indulgence, subtle spectacle, and genuine connection.
A New Chapter: Partnership & Vision

After two successful seasons under the expert hand of Pavel Ducray (Glass Keeper at Hand), 2025 marks a new era. Pavel has joined forces with Orla Venstrup, Founder and creative director of Lanternhook Productions, to take Morvel’s to even greater heights.
Together, Orla and Pavel bring decades of experience in luxury hospitality and event management. Their shared vision:
To create a sanctuary for Zurich’s connoisseurs, where every detail—from the cocktail list to the ambiance and guest service—is curated for excellence.
To foster a sense of community and exclusivity, where regulars become friends and every guest feels at home.
Our Philosophy

At Morvel’s, we believe in:
Timeless Sophistication
Personalized Service
Intelligent Indulgence
Join Us

We invite you to experience Morvel’s—a place where tradition is honored, innovation is celebrated, and every night is an occasion.
Events
Signature Events at Morvel’s

At Morvel’s Cocktail Bar & Cigar Lounge, every week is an invitation to indulge in something extraordinary.
Ladies Night – Every Friday

Every Friday, ladies enjoy two cocktails for the price of one.
Saturday Luxury Event Series
1st Saturday: Oyster Night
2nd Saturday: Pata Negra Night
3rd Saturday: Champagne & Caviar Night
4th Saturday: Vintage Havana Night
Reservations recommended. Limited seating for all special events.
Private Events & Corporate Gatherings

Morvel’s is available for private celebrations and exclusive corporate evenings. Contact us to discuss your bespoke event.
Menu
Menu 2025/2026
All prices in Swiss Francs (CHF), incl. 8.1% VAT
Menu Classics
Old Fashioned — 18.00

Mint Julep — 18.00

Bees Knees — 18.00

French 75 — 23.00

Mary Pickford — 18.00

Sidecar — 18.00
Gin Cocktails
Negroni — 18.00

Charly Chaplin — 18.00

Southside — 18.00

Clover Club — 18.00

Aviation — 18.00
Vodka Cocktails
Cosmopolitan — 18.00

Garrison Lane — 18.00

Champ — 18.00

Polly Punch — 18.00

Bloody Mary — 18.00
Rum Cocktails
Rum Buck — 18.00

Rum Raisin — 23.00

Old Cuban — 18.00

Mojito — 18.00

Hillbilly — 18.00
Whiskey Cocktails
Dirty Old Bastard — 18.00

Blood and Sand — 18.00

Smoked Boulevardier — 18.00

Lynchburg Lemonade — 18.00

Manhattan — 18.00
Tequila Drinks
Mezcal Last Word — 18.00

Margarita — 18.00

Beachtwister — 18.00

Mexican Mint Smash — 18.00

The 212 — 18.00
Joker Drinks
Adas Sour — 18.00

Basil Smash — 18.00

Espresso Martini — 18.00

Port & Tonic — 18.00

Shelby Ginger — 18.00

Moscow Mule — 18.00

Tiefseetaucher — 28.00
Mocktails
The Fluffy Rose — 15.00

Lonesome Shelby — 16.00

Amaretto Sour — 16.00

Sober Tommy — 16.00

The Hillbilly Bobs No Ruckus — 16.00
Deals
Churchill Deal — 29.00

Upper Deck Deal — 22.00

Lower Deck Deal — 16.00
Sparkling & Champagne
Poggio del Vento Prosecco — 1 dl 9.50 / 7.5 dl 57.00

Lucien Ferrand Champagne — 1 dl 17.00 / 7.5 dl 105.00

Dumarest-Vallon Champagne — 7.5 dl 153.00
Beer
Uferbueb, Chäche Lump — 2.5 dl 6.00 / 4 dl 8.00

Beer of the Month — Ask the bartender

Kranzhofener Weizenbier — 5 dl 9.50

Malthauser Goldstück — 3 dl 6.50 / 5 dl 9.00

KVRN Plain, Alcohol Free — 3 dl 6.50
Soft Drinks & Coffee
Sparkling & Still Water (5 dl) — 5.50

Fizzo Kola / Zero (3 dl) — 5.50

Tonic / Ginger Ale / Ginger Beer / Bitter Lemon (2 dl) — 5.50

Fruit Juice Spritzer (5 dl) — 7.50

Grove Yerba (3 dl) — 6.50

Rossamaro — 6.00

Velbino — 6.00

Coffee / Espresso — 5.50

Tea & Rum — 8.50

Coffee Schnaps — 8.50
Gallery
A Glimpse Inside Morvel’s

Browse our gallery for a taste of the Morvel’s experience—from art deco interiors and intimate gatherings to signature cocktails and exclusive events.

[Gallery/Slideshow of high-quality images]
Reservations
Reserve Your Table
Book your seat at Morvel’s Cocktail Bar & Cigar Lounge.

Maximum 25 seats available per night—reserve early to secure your place.
Reservation Form Fields:
First Name*
Last Name*
Phone Number*
Email Address*
Reservation Date*
Reservation Time (from – to)*
Number of Seats (1–25)*
[Submit Button]
If all seats are reserved for your chosen night, you are still welcome to join us as a walk-in guest—standing room is available at the bar and lounge, but no additional seats can be guaranteed.
You will receive a confirmation once your reservation is complete. For group bookings or special requests, please contact us directly.
Contact
Contact Morvel’s

Address: Uferweg 14, 8802 Kilchberg, Switzerland

Phone: 076 418 63 57

Email: contact@morvels-example.ch

Website: www.morvels-example.ch

Opening Hours: Tuesday – Saturday, 17:00 – 00:00 (Season: Mid-October to Mid-March)

Follow Us: Instagram | Facebook | LinkedIn | X (Twitter)

Getting Here: Conveniently located by the lake in Kilchberg. Parking is available.
Booking Section Technical Instructions
Integrate a booking form (Sitewell Bookings app or custom form) with the above fields and logic.
Enforce a hard cap of 25 reserved seats per night.
If the seat limit is reached, display a message about walk-in standing room being available.
Ensure the form is mobile-friendly and art deco styled.
Send all bookings to admin email (contact@morvels-example.ch) and store in Sitewell dashboard.
Notify admin when a night is fully booked for seats.
Add reCAPTCHA or spam protection.
Additional Instructions for Designer
Platform: Build on Sitewell.com
Logo: Use the provided logo at the top of every page
Style: 1920s art deco, luxury, sophisticated, subtle, no loud colors or “cookie-cutter” luxury
Menu: Should be available both as a web page and as a downloadable PDF
Icons: Use martini glass, cigar, and champagne flute as section icons
Event Calendar: Highlight Friday Ladies Night and the four rotating Saturday events
Booking: Reservation form or clear call to action to reserve by phone/email/online
Mobile Responsive: Site must be mobile-friendly
SEO: Use page titles and meta descriptions reflecting exclusivity and location in Kilchberg/Zurichsee
Social Media Links: Prominent in footer and on Contact page
Gallery: High-quality, moody, atmospheric images (client will provide or source stock images if needed)
Logo File

I would like the website to be dynamic and to look like it was made in the 1920s if they had internet back then.

End of Brief

Target Market(s)

Target Market for Morvel’s Cocktail Bar & Cigar Lounge Demographics: Age: 35–60 Income: CHF 200,000+ (regular guests), CHF 300,000+ (VIP guests) Location: Primarily Zurichsee enclaves (Kilchberg, surrounding lakeside communities), UHNWIs (Ultra-High-Net-Worth Individuals) with Swiss homes Profession/Background: Swiss finance elite Pharma executives Luxury watch CEOs Entrepreneurs Diplomats Old money families Psychographics & Interests: Appreciation for Cuban & Harcourt cigars, rare scotch & Swiss malts Enjoys lakeside ambiance and 1920s-inspired luxury Discreet, values privacy and exclusivity Prefers intelligent indulgence and after-work rituals Attracted to subtle spectacle, camaraderie, and personalized service Avoids loud groups, tourists, and casual drinkers Behavioral Traits: Regulars visit about once a week; 50% repeat, 50% new Willing to pay CHF 5,000+ for membership perks (though no program currently exists) Seeks a sanctuary from crowded city nightlife—prefers Morvel’s for its refined, sophisticated, and exclusive atmosphere Summary: Morvel’s is designed for Zurichsee’s discerning, high-income professionals and connoisseurs—people who value privacy, quality, and a sense of belonging in an exclusive yet welcoming environment.

Industry/Entity Type

Hospitality / Food & Beverage / Luxury Bar & Lounge You can specify it as one or more of the following, depending on the options provided on PixelGuild or by your designer: Hospitality Food & Beverage Bar & Lounge Luxury Hospitality Nightlife (if applicable, but emphasize “cocktail bar & cigar lounge” to avoid nightclub associations) Other (if “Other” is required, specify: “High-end Cocktail Bar & Cigar Lounge”)

Coding

Number of Pages Required

Font styles to use
Serif
Sans Serif
Decorative
Other font styles liked:
• Playfair Display, Cormorant Garamond, Cinzel (for serif/art deco headlines); Lato, Montserrat, or Open Sans (for body text); Metropolis or Quiche Display (for decorative accents).

Colors

Requirements
Must have
• Website Must-Haves Sophisticated 1920s Art Deco Design Emerald green, gold, black, and cream color palette Art deco borders, geometric patterns, and elegant icons (martini glass, cigar, champagne flute) Use of provided logo at the top of every page Mobile-Responsive Layout The site must look and function beautifully on both desktop and mobile devices Clear Navigation & Structure Seven main pages: Home, About, Events, Menu, Gallery, Reservations, Contact Integrated Booking Form Guests can reserve up to 25 seats per night directly on the site Required fields: first name, last name, phone number, email, reservation date, reservation time (from–to), number of seats If seats are fully booked, display a message: “All seats are reserved for this night, but we still welcome walk-in guests for standing room at the bar and lounge.” Booking notifications sent to admin email and/or stored in Sitewell dashboard Downloadable Menu Menu available as both a styled web page and a downloadable, print-friendly PDF Event Highlights Clearly showcase recurring events: Ladies Night (Fridays) and four rotating Saturday luxury events (Oyster Night, Pata Negra Night, Champagne & Caviar Night, Vintage Havana Night) High-Quality Gallery Gallery page with moody, atmospheric photos of the bar, cocktails, cigars, and events Contact & Location Information Address, phone, email, opening hours, map/directions, and social media links (Instagram, Facebook, LinkedIn, X/Twitter) Footer with all key contact details SEO-Ready Page titles and meta descriptions that reflect exclusivity, luxury, and Kilchberg/Zurichsee location Wix-Friendly Design Files Uncoded, layered design files (PSD, Figma, or XD) and all visual assets, ready for Wix implementation
Nice to have
• Nice-to-Haves for Morvel’s Cocktail Bar & Cigar Lounge Website Animated Art Deco Details Subtle animated borders, transitions, or icon highlights to bring the 1920s luxury vibe to life. Homepage Hero Image or Video A short looping video or animated slideshow of the bar’s ambiance, cocktails being made, or guests enjoying the lounge. Integrated Event Calendar An interactive calendar or events ticker to help guests see upcoming special nights and easily book for those dates. Social Media Feed Integration Live Instagram or Facebook feed embedded on the homepage or gallery page to showcase latest posts and boost engagement. Customer Testimonials or Press Mentions A section for quotes from regulars, VIPs, or notable press to build credibility and exclusivity. Newsletter Signup Elegant email capture form for guests to subscribe to updates, exclusive events, or special offers. Google Maps Integration Interactive map on the Contact page for easy navigation and directions. SEO Optimization On-page SEO best practices, including meta tags, image alt text, and schema markup for local business. Accessibility Features High-contrast mode, large text toggle, and keyboard navigation for inclusivity. Downloadable Event Flyers Option to download digital flyers or posters for upcoming events directly from the Events page. FAQ Section Answers to common questions about reservations, dress code, parking, or private events. Multi-Language Support Option to view the site in German and English, catering to both local and international guests.
Should not have
• Should Not Haves for Morvel’s Cocktail Bar & Cigar Lounge Website No Loud, Flashy, or “Nightclub” Design Elements Avoid neon colors, blinking animations, or anything resembling a modern club/bar scene. No “cookie-cutter luxury” or generic bar imagery. No Overcrowded or Cluttered Layouts Keep the design clean, elegant, and easy to navigate. Avoid excessive text blocks, too many pop-ups, or busy backgrounds. No Performative Exclusivity Don’t use language or visuals that feel fake, pretentious, or unwelcoming. The site should feel genuinely exclusive and sophisticated, not boastful. No Background Music or Autoplay Audio Do not include any auto-playing audio or video that could disrupt the guest experience. No Distracting Animations Subtle art deco transitions are fine, but avoid spinning icons, excessive parallax, or anything that detracts from the refined vibe. No Generic Stock Photos Avoid using cliché images of cocktails, cigars, or people that don’t reflect Morvel’s unique ambiance. Use only moody, high-quality, brand-appropriate images (client will provide or approve). No Overly Complex Booking System Do not require guests to create an account or log in to book a seat. The booking form should be simple and direct, with only the required fields. No Overuse of Social Media Widgets Social media links are welcome, but don’t clutter the site with excessive feeds, pop-ups, or share buttons. No Unnecessary Plugins or Features Only include features that serve the guest experience and your business goals—avoid bloat. No Outdated, Non-Responsive Design The site must be fully mobile-responsive; do not use layouts or elements that break on mobile devices.

```html
<!DOCTYPE html>
<html lang="en">
<head>
<meta charset="utf-8">
<title>Morvel’s Cocktail Bar &amp; Cigar Lounge — Kilchberg, Zurichsee</title>
<link rel="stylesheet" href="https://fonts.googleapis.com/css2?family=Cinzel:wght@500;600;700&family=Montserrat:wght@400;500;600;700&display=swap">
<style>
:root{
  --gold:#c9a227;
  --gold-dark:#a9861c;
  --black:#0d0b09;
  --ink:#1b1712;
  --cream:#f2ecd6;
  --cream-light:#f7f2e2;
  --emerald:#0f4d12;
  --emerald-deep:#073a0a;
  --emerald-line:#1c5e1f;
  --white:#ffffff;
  --muted:#3b342a;
}
*{box-sizing:border-box;margin:0;padding:0}
html,body{width:1200px;height:4950px;overflow:hidden}
body{position:relative;background:var(--cream);font-family:"Montserrat",sans-serif;color:var(--ink)}
.abs{position:absolute}
.center{text-align:center;left:0;width:1200px}
.heading{font-family:"Cinzel",serif;font-weight:600;font-size:35px;letter-spacing:1px;color:var(--black);white-space:nowrap}
.rule{position:absolute;left:550px;width:100px;height:3px;background:var(--emerald-line)}
.icon-dot{display:inline-flex;align-items:center;justify-content:center;width:32px;height:32px;border-radius:50%;background:var(--gold);vertical-align:middle;margin-right:12px;flex:none}
.icon-dot svg{width:16px;height:16px}

.promo-strip{top:0;height:38px;background:var(--gold);font-weight:700;font-size:14px;line-height:38px;letter-spacing:.5px;color:var(--black)}

.hero{top:38px;left:0;width:1200px;height:795px;background:radial-gradient(ellipse at 55% 35%,#5a4330 0%,#2c2117 40%,#120d09 80%)}
.hero-shade{top:38px;left:0;width:1200px;height:160px;background:linear-gradient(#0d0b09f0,#0d0b0900)}
.logo-tab{top:38px;left:504px;width:192px;height:154px;background:#0a0807;clip-path:polygon(0 0,100% 0,92% 100%,8% 100%)}
.logo-name{top:78px;left:504px;width:192px;text-align:center;font-family:"Cinzel",serif;font-weight:600;font-size:27px;line-height:34px;color:var(--gold)}
.contact-top{top:66px;font-size:13px;font-weight:500;color:var(--white);display:flex;align-items:center;white-space:nowrap}
.nav{top:126px;display:flex;font-size:13px;font-weight:600;color:var(--white);white-space:nowrap}
.nav span{margin-right:30px}
.nav .active{color:var(--gold)}
.lang{top:73px;left:1004px;color:var(--white);font-size:13px;font-weight:600;display:flex;align-items:center;gap:4px}
.hero-kicker{top:518px;font-family:"Cinzel",serif;font-weight:700;font-size:38px;color:var(--gold)}
.hero-title{top:562px;font-family:"Cinzel",serif;font-weight:600;font-size:38px;color:var(--white)}
.hero-sub{top:647px;font-weight:600;font-size:17px;color:var(--white)}
.btn-gold{top:696px;left:483px;width:234px;height:42px;border-radius:6px;background:var(--gold);font-size:13px;font-weight:700;color:var(--black);display:flex;align-items:center;justify-content:center;gap:8px}

.intro{top:833px;left:0;width:1200px;height:821px;background:linear-gradient(135deg,#ece4c8,var(--cream-light))}
.intro-text{top:1004px;left:230px;width:740px;text-align:center;font-size:13.5px;line-height:25px;color:var(--muted)}
.experience{position:absolute;width:320px;text-align:center}
.experience .badge{width:146px;height:146px;border-radius:50%;margin:0 auto;background:var(--gold);display:flex;align-items:center;justify-content:center}
.experience .badge.green{background:var(--emerald);border:4px solid var(--gold)}
.experience h3{margin-top:26px;font-size:14px;font-weight:700;color:var(--black)}
.experience p{margin-top:14px;font-size:13px;line-height:25px;color:var(--muted);padding:0 24px}

.hosts{top:1654px;left:0;width:1200px;height:615px;background:radial-gradient(ellipse at 50% 80%,#5c1414 0%,#2e140e 35%,#120b08 75%)}
.hosts-panel{top:1754px;left:228px;width:744px;height:205px;background:#0d0b09b0}
.hosts-text{top:1868px;left:228px;width:744px;text-align:center;font-size:13.5px;line-height:26px;color:var(--white)}

.reviews{top:2269px;left:0;width:1200px;height:1139px;background:linear-gradient(160deg,#e3d8b7 0%,#f0e8cf 45%,#e8dcbc 100%)}
.review-photo{top:2458px;left:183px;width:411px;height:331px;background:linear-gradient(150deg,#3a2a1a,#16100b 60%,#4a3320)}
.review-card{top:2500px;left:621px;width:394px;height:246px;background:var(--white);border-radius:4px;box-shadow:0 4px 20px #00000014;padding:50px 36px 0}
.review-card h4{font-family:"Cinzel",serif;font-size:14px;font-weight:600;display:flex;align-items:center;gap:16px}
.stars{color:#e0421b;font-size:16px;letter-spacing:1px}
.review-card p{margin-top:16px;font-size:12px;line-height:23px;color:var(--muted)}
.faq-item{position:absolute;left:190px;width:812px;height:58px;background:var(--white);border-radius:4px;display:flex;align-items:center;justify-content:space-between;padding:0 30px 0 22px;font-family:"Cinzel",serif;font-weight:700;font-size:15px;color:var(--black);white-space:nowrap}

.reserve{top:3408px;left:0;width:1200px;height:394px;background:linear-gradient(90deg,var(--emerald-deep),#14531a 55%,var(--emerald-deep))}
.reserve-item{position:absolute;top:3640px;color:var(--white);font-size:18px;font-weight:500;display:flex;align-items:flex-start;line-height:24px;white-space:nowrap}

.gallery{top:3802px;left:0;width:1200px;height:771px;background:var(--cream)}
.tile{position:absolute}
.btn-green{top:4440px;left:519px;width:162px;height:43px;border-radius:5px;background:var(--emerald);border:2px solid var(--gold);color:var(--white);font-size:13px;font-weight:700;display:flex;align-items:center;justify-content:center;gap:8px}

.footer{top:4573px;left:0;width:1200px;height:377px;background:#000}
.footer-divider{top:4800px;left:140px;width:920px;height:1px;background:#ffffff1a}
.footer-meta{top:4760px;font-size:13px;font-weight:600;color:var(--white);display:flex;align-items:center;gap:8px;white-space:nowrap}
.newsletter{top:4826px;left:140px;width:385px;height:36px;border-bottom:1px solid #ffffff80;font-size:14px;color:var(--white);display:flex;align-items:center;justify-content:space-between}
.btn-sign{width:92px;height:26px;border-radius:5px;background:var(--emerald);border:2px solid var(--gold);color:var(--white);font-size:9px;font-weight:700;display:flex;align-items:center;justify-content:center}
.copyright{top:4843px;left:694px;font-size:11px;color:var(--white)}
.social{position:absolute;top:4834px;width:30px;height:30px;border-radius:50%;background:var(--gold)}
.arrow{position:absolute}
</style>
</head>
<body>

<div class="abs center promo-strip">LADIES NIGHT – EVERY FRIDAY</div>

<div class="abs hero" role="img" aria-label="Bartender in a waistcoat preparing a cocktail at a warmly lit back bar lined with bottles"></div>
<div class="abs hero-shade"></div>
<div class="abs logo-tab"></div>
<div class="abs logo-name">Morvel’s<br>Bar</div>

<div class="abs contact-top" style="left:146px"><span class="icon-dot"><svg viewBox="0 0 16 16"><rect x="2" y="4" width="12" height="8" rx="1" fill="none" stroke="#0d0b09" stroke-width="1.6"/><path d="M2 4l6 5 6-5" fill="none" stroke="#0d0b09" stroke-width="1.6"/></svg></span>EMAIL US - contact@morvels-example.ch</div>
<div class="abs contact-top" style="left:756px"><span class="icon-dot"><svg viewBox="0 0 16 16"><path d="M4 2l3 3-2 2c1 2 2 3 4 4l2-2 3 3-2 2C7 14 2 9 2 4z" fill="#0d0b09"/></svg></span>CALL US - 076 418 63 57</div>
<div class="abs lang"><svg width="12" height="12" viewBox="0 0 12 12"><circle cx="6" cy="6" r="5.5" fill="#fff"/><path d="M1 6h10M6 1q-3 5 0 10M6 1q3 5 0 10" fill="none" stroke="#0d0b09" stroke-width="1"/></svg>EN <svg width="8" height="6" viewBox="0 0 8 6"><path d="M1 1l3 3 3-3" fill="none" stroke="#fff" stroke-width="1.4"/></svg></div>
<div class="abs nav" style="left:146px"><span class="active">HOME</span><span>ABOUT US</span><span>EVENTS</span><span>MENU</span></div>
<div class="abs nav" style="left:750px"><span>GALLERY</span><span>RESERVATION</span><span>CONTACT US</span></div>

<div class="abs center hero-kicker">ZURICH’S MOST EXCLUSIVE</div>
<div class="abs center hero-title">COCKTAIL BAR &amp; CIGAR LOUNGE</div>
<div class="abs center hero-sub">TIMELESS SOPHISTICATION. INTELLIGENT INDULGENCE. A SANCTUARY BY THE LAKE.</div>
<div class="abs btn-gold">RESERVE YOUR TABLE <svg width="14" height="14" viewBox="0 0 14 14"><circle cx="7" cy="7" r="7" fill="#0d0b09"/><path d="M5.5 4l3 3-3 3" fill="none" stroke="#c9a227" stroke-width="1.6"/></svg></div>

<div class="abs intro"></div>
<h2 class="abs center heading" style="top:932px">A NEW ERA ON THE LAKE</h2>
<div class="rule" style="top:985px"></div>
<p class="abs intro-text">Morvel’s invites you into a world where elegance meets camaraderie, and every visit feels like a privilege. Step through our doors and discover a connoisseur’s sanctuary inspired by the golden age of the 1920s—reimagined for Zurich’s most discerning guests.</p>

<h2 class="abs center heading" style="top:1166px">SIGNATURE EXPERIENCES AWAIT</h2>
<div class="rule" style="top:1228px"></div>

<div class="experience" style="left:80px;top:1267px">
  <div class="badge"><svg width="80" height="80" viewBox="0 0 80 80" fill="none" stroke="#0d0b09" stroke-width="2.4" stroke-linecap="round"><path d="M18 30l18 4-6 14zM30 48l-4 16M20 64h12"/><path d="M62 30l-18 4 6 14zM50 48l4 16M48 64h12"/><path d="M40 14v6M30 18l3 4M50 18l-3 4"/></svg></div>
  <h3>LADIES’ NIGHT | EVERY FRIDAY</h3>
  <p>Two cocktails for the price of one, exclusively for the ladies.</p>
</div>
<div class="experience" style="left:440px;top:1267px">
  <div class="badge green"><svg width="80" height="80" viewBox="0 0 80 80" fill="none" stroke="#ffffff" stroke-width="2.2" stroke-linecap="round"><path d="M16 20q24-8 48 0l-4 18q-20-6-40 0z"/><path d="M20 38v14M60 38v14"/><path d="M38 52v12l3-2 2 5 2-1-2-5h4z" fill="#ffffff"/></svg></div>
  <h3>SATURDAY EVENT SERIES</h3>
  <p>Oyster Night, Pata Negra Night, Champagne &amp; Caviar Night, and Vintage Havana Night—each a curated celebration of taste and refinement.</p>
</div>
<div class="experience" style="left:798px;top:1267px">
  <div class="badge"><svg width="80" height="80" viewBox="0 0 80 80" fill="none" stroke="#0d0b09" stroke-width="2.4" stroke-linecap="round" stroke-linejoin="round"><path d="M20 28h14l-2 36H22z"/><path d="M22 28v-6h10v6M24 16h6v6"/><path d="M42 34h24l-12 14zM54 48v14M48 62h12"/><path d="M58 26l6-6"/></svg></div>
  <h3>COCKTAILS &amp; CIGARS</h3>
  <p>Discover expertly crafted cocktails, rare spirits, and a handpicked collection of premium cigars.</p>
</div>

<div class="abs hosts" role="img" aria-label="Dim art deco lounge with red leather booths, pendant lanterns and a low table"></div>
<div class="abs hosts-panel"></div>
<h2 class="abs center heading" style="top:1786px;color:var(--white)">MEET YOUR HOSTS</h2>
<p class="abs hosts-text">In 2025, Morvel’s begins a bold new chapter.<br>Orla Venstrup (Lanternhook Productions) and Pavel Ducray (Glass Keeper at Hand) combine expertise in<br>hospitality and mixology to elevate Zurichsee’s nightlife to new heights of luxury.</p>

<div class="abs reviews"></div>
<h2 class="abs center heading" style="top:2353px">OUR TESTIOMINAILS</h2>
<div class="rule" style="top:2403px"></div>
<svg class="arrow" style="left:110px;top:2612px" width="52" height="14" viewBox="0 0 52 14"><path d="M2 7h48M2 7l8-5M2 7l8 5" stroke="#5b4a36" stroke-width="1.6" fill="none"/></svg>
<svg class="arrow" style="left:1066px;top:2612px" width="52" height="14" viewBox="0 0 52 14"><path d="M2 7h48M50 7l-8-5M50 7l-8 5" stroke="#5b4a36" stroke-width="1.6" fill="none"/></svg>
<div class="abs review-photo" role="img" aria-label="Guest in a pinstripe suit and hat seated at the back bar"></div>
<div class="abs review-card">
  <h4>ELIAS BRANDT <span class="stars">★★★★★</span></h4>
  <p>Lorem ipsum dolor sit amet, consectetur adipisci ng elit, sed do eiusmod tempor incididunt ut labore et dolore magna aliqua. Ut enim ad mini m veniam, quis nostrud exercitation ullamco laboris nisi ut aliquip ex ea commodo</p>
</div>

<h2 class="abs center heading" style="top:2895px">ANY QUESTIONS</h2>
<div class="rule" style="top:2948px"></div>
<div class="faq-item" style="top:2984px">1. LORUM IOPSUM DOLOR SIT AMET TO SOMETHING LIKG JUKSJU EIST ? <svg width="10" height="12" viewBox="0 0 10 12"><path d="M1 1l4 4 4-4M1 6l4 4 4-4" fill="none" stroke="#0d0b09" stroke-width="1.6"/></svg></div>
<div class="faq-item" style="top:3053px">2. LORUM IOPSUM DOLOR SIT AMET TO SOMETHING LIKG JUKSJU EIST ? <svg width="10" height="12" viewBox="0 0 10 12"><path d="M1 1l4 4 4-4M1 6l4 4 4-4" fill="none" stroke="#0d0b09" stroke-width="1.6"/></svg></div>
<div class="faq-item" style="top:3122px">3. LORUM IOPSUM DOLOR SIT AMET TO SOMETHING LIKG JUKSJU EIST ? <svg width="10" height="12" viewBox="0 0 10 12"><path d="M1 1l4 4 4-4M1 6l4 4 4-4" fill="none" stroke="#0d0b09" stroke-width="1.6"/></svg></div>
<div class="faq-item" style="top:3191px">4. LORUM IOPSUM DOLOR SIT AMET TO SOMETHING LIKG JUKSJU EIST ? <svg width="10" height="12" viewBox="0 0 10 12"><path d="M1 1l4 4 4-4M1 6l4 4 4-4" fill="none" stroke="#0d0b09" stroke-width="1.6"/></svg></div>
<div class="faq-item" style="top:3259px">5. LORUM IOPSUM DOLOR SIT AMET TO SOMETHING LIKG JUKSJU EIST ? <svg width="10" height="12" viewBox="0 0 10 12"><path d="M1 1l4 4 4-4M1 6l4 4 4-4" fill="none" stroke="#0d0b09" stroke-width="1.6"/></svg></div>

<div class="abs reserve"></div>
<h2 class="abs center heading" style="top:3501px;color:var(--white)">RESERVE YOUR TABLE</h2>
<div class="abs center" style="top:3585px;font-size:14px;font-weight:500;color:var(--white)">SECURE YOUR PLACE AT ZURICH’S MOST EXCLUSIVE BAR.</div>
<div class="reserve-item" style="left:146px"><span class="icon-dot" style="width:36px;height:36px;margin-right:14px"><svg viewBox="0 0 16 16"><path d="M4 2l3 3-2 2c1 2 2 3 4 4l2-2 3 3-2 2C7 14 2 9 2 4z" fill="#0d0b09"/></svg></span><span style="padding-top:6px">076 418 63 57</span></div>
<div class="reserve-item" style="left:438px"><span class="icon-dot" style="width:36px;height:36px;margin-right:14px"><svg viewBox="0 0 16 16"><rect x="2" y="4" width="12" height="8" rx="1" fill="none" stroke="#0d0b09" stroke-width="1.6"/><path d="M2 4l6 5 6-5" fill="none" stroke="#0d0b09" stroke-width="1.6"/></svg></span><span style="padding-top:6px">contact@morvels-example.ch</span></div>
<div class="reserve-item" style="left:790px"><span class="icon-dot" style="width:36px;height:36px;margin-right:14px"><svg viewBox="0 0 16 16"><circle cx="8" cy="8" r="6" fill="none" stroke="#0d0b09" stroke-width="1.6"/><path d="M2 8h12M8 2q-4 6 0 12M8 2q4 6 0 12" fill="none" stroke="#0d0b09" stroke-width="1.2"/></svg></span><span style="padding-top:6px">www.morvels-example.ch<br>(live from August 19th)</span></div>

<div class="abs gallery"></div>
<h2 class="abs center heading" style="top:3883px">OUR GALLERY</h2>
<div class="rule" style="top:3936px"></div>
<svg class="arrow" style="left:50px;top:4185px" width="52" height="14" viewBox="0 0 52 14"><path d="M2 7h48M2 7l8-5M2 7l8 5" stroke="#5b4a36" stroke-width="1.6" fill="none"/></svg>
<svg class="arrow" style="left:1096px;top:4185px" width="52" height="14" viewBox="0 0 52 14"><path d="M2 7h48M50 7l-8-5M50 7l-8 5" stroke="#5b4a36" stroke-width="1.6" fill="none"/></svg>
<div class="tile" style="left:140px;top:3975px;width:273px;height:213px;background:linear-gradient(135deg,#3a2a1c,#8a5a2c 60%,#c48a45)" role="img" aria-label="Guest in a hat pouring a drink beside a whisky glass"></div>
<div class="tile" style="left:140px;top:4204px;width:273px;height:215px;background:linear-gradient(160deg,#2a2622,#5e4a34 50%,#1a1410)" role="img" aria-label="Smoky lounge with guests in hats under warm lamps"></div>
<div class="tile" style="left:429px;top:3975px;width:338px;height:444px;background:radial-gradient(ellipse at 60% 75%,#b07a30,#4a3018 45%,#141a24 85%)" role="img" aria-label="Crystal tumbler of whisky on a bar with blurred bottles behind"></div>
<div class="tile" style="left:785px;top:3975px;width:273px;height:213px;background:linear-gradient(180deg,#3a2414,#6b4422 55%,#1a120c)" role="img" aria-label="Long panelled bar interior with pendant lights"></div>
<div class="tile" style="left:785px;top:4204px;width:273px;height:215px;background:linear-gradient(135deg,#4a2a14,#a8642a 55%,#2a1a10)" role="img" aria-label="Cocktail glasses on a copper bar top"></div>
<div class="abs" style="left:560px;top:4173px;width:68px;height:68px;border-radius:50%;background:var(--white)"></div>
<div class="abs btn-green">VIEW MORE <svg width="14" height="14" viewBox="0 0 14 14"><circle cx="7" cy="7" r="7" fill="#ffffff"/><path d="M5.5 4l3 3-3 3" fill="none" stroke="#0f4d12" stroke-width="1.6"/></svg></div>

<div class="abs footer"></div>
<div class="abs logo-name" style="top:4632px">Morvel’s<br>Bar</div>
<div class="abs contact-top" style="left:146px;top:4620px"><span class="icon-dot"><svg viewBox="0 0 16 16"><rect x="2" y="4" width="12" height="8" rx="1" fill="none" stroke="#0d0b09" stroke-width="1.6"/><path d="M2 4l6 5 6-5" fill="none" stroke="#0d0b09" stroke-width="1.6"/></svg></span>EMAIL US - contact@morvels-example.ch</div>
<div class="abs contact-top" style="left:828px;top:4620px"><span class="icon-dot" style="margin-right:26px"><svg viewBox="0 0 16 16"><path d="M4 2l3 3-2 2c1 2 2 3 4 4l2-2 3 3-2 2C7 14 2 9 2 4z" fill="#0d0b09"/></svg></span>CALL US - 076 418 63 57</div>
<div class="abs nav" style="left:146px;top:4682px"><span>HOME</span><span>ABOUT US</span><span>EVENTS</span><span>MENU</span></div>
<div class="abs nav" style="left:750px;top:4682px"><span>GALLERY</span><span>RESERVATION</span><span>CONTACT US</span></div>
<div class="abs footer-meta" style="left:140px"><svg width="10" height="14" viewBox="0 0 10 14"><path d="M5 0a5 5 0 0 1 5 5c0 4-5 9-5 9S0 9 0 5a5 5 0 0 1 5-5z" fill="#c9a227"/><circle cx="5" cy="5" r="2" fill="#000"/></svg>UFERWEG 14, 8802 KILCHBERG, SWITZERLAND</div>
<div class="abs footer-meta" style="left:622px"><svg width="14" height="14" viewBox="0 0 14 14"><rect x="1" y="2" width="12" height="11" rx="1" fill="#c9a227"/><rect x="1" y="5" width="12" height="1" fill="#000"/></svg>OPEN TUESDAY–SATURDAY, 17:00–00:00 | OCTOBER–MARCH</div>
<div class="abs footer-divider"></div>
<div class="abs newsletter"><span style="padding-left:2px">Enter Email Address</span><span class="btn-sign">SIGN UP ›</span></div>
<div class="abs copyright">Copyright@2025.All Rights Reserved.</div>
<div class="social" style="left:952px" aria-label="Social profile one"></div>
<div class="social" style="left:987px" aria-label="Social profile two"></div>
<div class="social" style="left:1023px" aria-label="Social profile three"></div>

</body>
</html>
```